Heron Property Inspection business card

I am the principal inspector of Heron Property Inspections. I serve Northern Virginia from Winchester to Arlington.Associate, Federated Guild of Dwelling Examiners (FGDE)Graduate, FGDE Home Inspectors CourseNational Association of Home Inspectors ExamI'd like the business card to look more professional than comical.I pulled the attached picture off the web. I'd like to have something like that or an image of a house as my logo on the cards.

Target Market(s)

Persons who recently purchased a home.

Industry/Entity Type

Business

Contact Information for Business Card

Bob AllenBadger Home Inspections, LLC.4455 River RoadBluemont, Virginia 20135cell: 703-231-6680e-mail: tkmarlow@postvale.net

Font styles to use
Serif
Sans Serif

Requirements
Must have
• I'd like to have a logo, something that identifies me as a home inspector. The attached images are something that I'd like to have incorporated into my business card logo.
Nice to have
• I'd like a sketch of a house and/or a magnifying glass showing a house being inspected. The attached images are used as a suggestion only, I do not own the images.
Should not have
• Gimmicky stuff. I want to appear professional and trustworthy.

```html
<!DOCTYPE html>
<html lang="en">
<head>
<meta charset="utf-8">
<title>Heron Property Inspections – Business Card</title>
<link href="https://fonts.googleapis.com/css2?family=Arimo:wght@400;700&display=swap" rel="stylesheet">
<style>
  :root {
    --page-bg: #e4ddd3;
    --card-bg: #f1f0ee;
    --card-edge: #d6d3ce;
    --navy: #1f4674;
    --teal: #186f80;
    --ink: #2d2d2d;
    --icon-glyph: #ffffff;
  }
  * { margin: 0; padding: 0; box-sizing: border-box; }
  html, body { width: 1200px; height: 970px; overflow: hidden; }
  body {
    background: var(--page-bg);
    font-family: "Arimo", Arial, sans-serif;
    position: relative;
  }
  .business-card {
    position: absolute;
    left: 60px; top: 185px;
    width: 1080px; height: 600px;
    background: var(--card-bg);
    border: 1px solid var(--card-edge);
    border-radius: 40px;
  }
  .brand {
    position: absolute;
    left: 40px; width: 470px;
    top: 205px;
    text-align: center;
    color: var(--navy);
    font-weight: 700;
  }
  .brand-dot {
    display: block;
    width: 70px; height: 70px;
    margin: 0 auto 22px;
    border-radius: 50%;
    background: var(--navy);
  }
  .brand-name { font-size: 46px; line-height: 1.05; letter-spacing: -0.5px; }
  .brand-company { font-size: 32px; line-height: 1.3; }
  .divider {
    position: absolute;
    left: 547px; top: 105px;
    width: 3px; height: 390px;
    background: var(--navy);
  }
  .contact {
    position: absolute;
    left: 614px; top: 168px;
    color: var(--ink);
  }
  .employee-name { font-size: 47px; color: var(--teal); font-weight: 400; line-height: 1; }
  .employee-title { font-size: 21px; margin-top: 6px; }
  .contact-list { list-style: none; margin-top: 44px; }
  .contact-list li {
    display: flex; align-items: flex-start;
    font-size: 27px; line-height: 29px;
    margin-bottom: 10px;
  }
  .contact-list svg { flex: none; width: 26px; height: 26px; margin: 2px 22px 0 0; }
</style>
</head>
<body>
  <main class="business-card">
    <div class="brand">
      <span class="brand-dot"></span>
      <div class="brand-name">Tim Marlow</div>
      <div class="brand-company">Heron Property Inspections, LLC</div>
    </div>

    <div class="divider"></div>

    <section class="contact">
      <h1 class="employee-name">Employee name</h1>
      <p class="employee-title">Managing Director</p>
      <ul class="contact-list">
        <li>
          <svg viewBox="0 0 26 26" aria-hidden="true">
            <rect width="26" height="26" rx="5" fill="#186f80"/>
            <rect x="8" y="5" width="10" height="16" rx="2" fill="none" stroke="#fff" stroke-width="2"/>
          </svg>
          703-555-0192
        </li>
        <li>
          <svg viewBox="0 0 26 26" aria-hidden="true">
            <rect width="26" height="26" rx="5" fill="#186f80"/>
            <rect x="5" y="8" width="16" height="11" fill="none" stroke="#fff" stroke-width="1.8"/>
            <polyline points="5,8 13,15 21,8" fill="none" stroke="#fff" stroke-width="1.8"/>
          </svg>
          tkmarlow@postvale.net
        </li>
        <li>
          <svg viewBox="0 0 26 26" aria-hidden="true">
            <rect width="26" height="26" rx="5" fill="#186f80"/>
            <path d="M13 21 C9 15 8 13 8 11 A5 5 0 0 1 18 11 C18 13 17 15 13 21 Z" fill="#fff"/>
            <circle cx="13" cy="11" r="2" fill="#186f80"/>
          </svg>
          <span>7182 Quarry LaneFernhill,<br>Virginia 20148</span>
        </li>
      </ul>
    </section>
  </main>
</body>
</html>
```